Web Design

We need a website for a company based in Doha Qatar called
Lumara Maid Service.

It is the number one maid cleaning service company, and we have branches all over qatar.

Luxury Cleaning Service Provider.

The color scheme is gold, yellow and black like the logo.

Before they get to the website, there is an intro video.

The website should depict luxury.

Target Market(s)

People who need maids at their houses.

Industry/Entity Type

Cleaning Service

Requirements
Must have
• Luxury, Sleek, Modern

The opening sequence is a video which I already have. Its too big to upload here so I am going to put it on youtube.

After the opening sequence, the home page should have a widescreen photo background and it should change every five seconds, the first background photo should be of qatar westbay skyline. Then the second background should be of maid photos in cleaning positions. Then the third background should be of cleaner photos etc.

We will send you all the tabs and all the content later.

```html
<!DOCTYPE html>
<html lang="en">
<head>
<meta charset="utf-8">
<title>Lumara Maid Service</title>
<link href="https://fonts.googleapis.com/css2?family=Cabin:wght@400;500&family=Open+Sans:wght@400;600&display=swap" rel="stylesheet">
<style>
:root{
  --gold:#e0901a;
  --gold-light:#f5a91f;
  --brown-dark:#2e1704;
  --brown:#4a2608;
  --brown-mid:#6b3a10;
  --ink:#1e1e1e;
  --text:#7a7a7a;
  --line:#dcdcdc;
  --white:#ffffff;
}
*{margin:0;padding:0;box-sizing:border-box}
html,body{width:929px;height:1200px;overflow:hidden;background:var(--white)}
body{position:relative;font-family:"Open Sans",sans-serif;color:var(--text)}
.abs{position:absolute}

/* header */
.brand{left:104px;top:38px;display:flex;align-items:center;gap:10px}
.brand-mark{width:30px;height:30px;border-radius:50%;background:var(--gold-light)}
.brand-name{font-family:"Cabin",sans-serif;font-size:22px;font-weight:500;color:var(--brown)}
.call{right:114px;top:52px;text-align:right;font-family:"Cabin",sans-serif}
.call-label{font-size:13px;color:var(--ink)}
.call-number{font-size:21px;color:var(--gold-light);line-height:1.2}

/* nav */
.nav{left:0;top:109px;width:929px;height:42px;background:linear-gradient(#5a2f0a,var(--brown-dark));display:flex;padding-left:105px}
.nav a{font-family:"Cabin",sans-serif;font-size:14px;color:var(--white);text-decoration:none;height:42px;line-height:42px;padding:0 17px;border-right:1px solid rgba(255,255,255,.12)}
.nav a:first-child{padding-left:19px}
.nav a:last-child{border-right:0}

/* hero */
.hero{left:0;top:151px;width:929px;height:356px;background:linear-gradient(100deg,#cfdbeb 0%,#dfe7f2 40%,#d3dfee 100%);border-bottom:1px solid #c9d3e0}
.hero-photo{left:380px;top:0;width:549px;height:356px;
  background:
    radial-gradient(ellipse 120px 150px at 58% 78%,rgba(122,144,190,.85),rgba(122,144,190,0)),
    radial-gradient(ellipse 70px 80px at 63% 32%,rgba(226,196,176,.7),rgba(226,196,176,0)),
    radial-gradient(ellipse 70px 110px at 32% 25%,rgba(160,196,222,.8),rgba(160,196,222,0)),
    linear-gradient(90deg,rgba(214,225,240,0) 0%,#c8d6ea 45%,#bccbe2 75%,#e2e9f3 100%)}
.hero-title{left:108px;top:108px;font-family:"Cabin",sans-serif;font-weight:400;font-size:28px;color:var(--gold)}
.hero-sub{left:108px;top:143px;font-family:"Cabin",sans-serif;font-size:18.5px;color:var(--ink)}
.hero-text{left:108px;top:172px;width:300px;font-size:9.5px;line-height:16px;color:#777}
.dots{left:108px;top:213px;display:flex;gap:4px}
.dots span{width:10px;height:10px;border-radius:50%;background:#111}

/* cards */
.card{top:532px;width:229px;height:183px;border:1px solid var(--line);background:linear-gradient(#fff 60%,#f3f3f3)}
.card-img{width:227px;height:102px}
.card h3{font-family:"Cabin",sans-serif;font-weight:400;font-size:16px;color:var(--gold);margin:12px 0 4px 13px}
.card p{font-size:9px;line-height:16px;margin:0 6px 0 13px;color:#777;letter-spacing:-.1px}

/* welcome */
.welcome{left:108px;top:750px;width:465px}
.welcome h2{font-family:"Cabin",sans-serif;font-weight:400;font-size:20px;color:var(--ink);margin-bottom:8px}
.welcome .lead{font-size:11.2px;line-height:16px;color:#555;margin:0 0 10px 3px}
.welcome p{font-size:9.2px;line-height:16px;color:#8a8a8a;margin:0 0 6px 3px}
.video-title{left:587px;top:751px;font-family:"Cabin",sans-serif;font-weight:400;font-size:19px;color:var(--brown-mid)}
.video{left:588px;top:783px;width:236px;height:150px;
  background:
    radial-gradient(ellipse 60px 70px at 25% 55%,rgba(120,190,170,.6),rgba(120,190,170,0)),
    linear-gradient(180deg,#cbb48e 0%,#cbb48e 18%,#3e3a38 30%,#2c2a29 80%,#6c6058 100%);}
.video-side{left:740px;top:783px;width:84px;height:150px;background:linear-gradient(90deg,rgba(220,226,236,0),#d9dfe8 40%,#eceae6)}
.play{left:692px;top:845px}

/* footer */
.footer{left:0;top:990px;width:929px;height:166px;background:linear-gradient(var(--brown-mid),var(--brown-dark))}
.fcol{top:1018px}
.fcol h4{font-family:"Cabin",sans-serif;font-weight:400;font-size:14px;color:var(--white);margin-bottom:6px}
.fcol a{display:block;font-size:9.5px;line-height:19px;color:var(--white);text-decoration:none}
.social{left:500px;top:1042px;display:flex;gap:3px}
.social span{width:21px;height:21px;border-radius:50%;background:var(--white)}
.fbrand{left:655px;top:1064px;display:flex;align-items:center;gap:8px}
.fbrand-mark{width:22px;height:22px;border-radius:50%;background:var(--gold-light)}
.fbrand-name{font-family:"Cabin",sans-serif;font-size:17px;color:var(--gold-light)}
.bottom{left:0;top:1156px;width:929px;height:44px;background:var(--brown-dark);border-top:1px solid #3d2209}
.copy{left:113px;top:1172px;font-size:9px;color:var(--white)}
</style>
</head>
<body>

<header>
  <div class="abs brand"><span class="brand-mark"></span><span class="brand-name">Lumara Maid Service</span></div>
  <div class="abs call"><div class="call-label">Call Us Now</div><div class="call-number">555.214.7730</div></div>
</header>

<nav class="abs nav">
  <a>Home</a><a>About Us</a><a>Services</a><a>Our Maid</a><a>Hire Maid</a><a>Videos</a><a>Testimonials</a><a>Contact Us</a>
</nav>

<section class="abs hero">
  <div class="abs hero-photo" role="img" aria-label="Maid in blue uniform and gloves wiping a window with a cloth"></div>
  <h1 class="abs hero-title">Lumara Provide Maid Service</h1>
  <div class="abs hero-sub">Phasellus felis dolor scelerisque</div>
  <p class="abs hero-text">Consequat nec porta vel lectus Nulla sit amet diam Duis non nunc libero a tempus libero lectus feugiat felis Morbi</p>
  <div class="abs dots"><span></span><span></span><span></span><span></span></div>
  <svg class="abs" style="left:42px;top:142px" width="24" height="52" viewBox="0 0 24 52"><polyline points="22,1 2,26 22,51" fill="none" stroke="#222" stroke-width="1.5"/></svg>
  <svg class="abs" style="left:843px;top:142px" width="24" height="52" viewBox="0 0 24 52"><polyline points="2,1 22,26 2,51" fill="none" stroke="#222" stroke-width="1.5"/></svg>
</section>

<article class="abs card" style="left:110px">
  <div class="card-img" role="img" aria-label="Woman in a kitchen giving a thumbs up in a cleaning glove" style="background:radial-gradient(ellipse 60px 40px at 68% 80%,rgba(190,205,230,.9),rgba(190,205,230,0)),linear-gradient(180deg,#d8c6bc 0%,#c9ab96 45%,#c79a6e 70%,#d8b48a 100%)"></div>
  <h3>Why Choose Our Maid</h3>
  <p>Etiam eu urna Sed porta Suspendisse quam leo molestie sed luctus quis feugiat in pede</p>
</article>
<article class="abs card" style="left:351px">
  <div class="card-img" role="img" aria-label="Maid making a bed with cream pillows" style="background:radial-gradient(ellipse 50px 60px at 88% 55%,rgba(150,145,140,.8),rgba(150,145,140,0)),linear-gradient(180deg,#d9c9a4 0%,#c9b385 45%,#e6dcc6 75%,#cfc2a8 100%)"></div>
  <h3>Services Provide</h3>
  <p>Etiam eu urna Sed porta Suspendisse quam leo molestie sed luctus quis feugiat in pede</p>
</article>
<article class="abs card" style="left:591px">
  <div class="card-img" role="img" aria-label="Smiling cleaner dusting a shelf with a feather duster" style="background:radial-gradient(ellipse 45px 60px at 18% 45%,rgba(120,80,60,.75),rgba(120,80,60,0)),radial-gradient(ellipse 40px 20px at 72% 45%,rgba(200,160,110,.7),rgba(200,160,110,0)),linear-gradient(90deg,#e9e3dc,#f1efea 50%,#eef0ea)"></div>
  <h3>Expert Cleaner Maids</h3>
  <p>Etiam eu urna Sed porta Suspendisse quam leo molestie sed luctus quis feugiat in pede</p>
</article>

<section class="abs welcome">
  <h2>Welcome to Lumara Maid Services</h2>
  <p class="lead">Phasellus felis dolor scelerisque a tempus eget lobortis id libero Donec scelerisque leo ac risus Praesent sit amet est In dictum dolor eu dictum porttitor</p>
  <p>Mauris vel lacus vitae felis vestibulum volutpat Etiam est nunc venenatis in tristique eu imperdiet ac nisl Cum sociis natoque penatibus et magnis dis parturient montes nascetur ridiculus mus In iaculis facilisis massa Etiam eu urna Sed porta Suspendisse quam leo molestie sed luctus quis.</p>
  <p>Feugiat in pede Fusce tellus Sed metus augue convallis et vehicula ut pulvinar eu ante Integer orci tellus tristique vitae consequat nec porta vel lectus Nulla sit amet diam Duis non nunc</p>
</section>

<h2 class="abs video-title">Watch Our Video</h2>
<div class="abs video" role="img" aria-label="Video still of a woman cleaning an oven door in gloves"></div>
<div class="abs video-side"></div>
<svg class="abs play" width="27" height="27" viewBox="0 0 27 27"><circle cx="13.5" cy="13.5" r="12" fill="rgba(0,0,0,.35)" stroke="#fff" stroke-width="2"/><polygon points="11,8.5 18.5,13.5 11,18.5" fill="#fff"/></svg>

<footer>
  <div class="abs footer"></div>
  <div class="abs fcol" style="left:109px"><h4>Company</h4><a>About Us</a><a>Why Chooose Us</a><a>Testimonials</a><a>Videos</a></div>
  <div class="abs fcol" style="left:228px"><h4>Our Services</h4><a>Home Cleaning</a><a>Deep Cleaning</a><a>Office Cleaning</a><a>Window Cleaning</a></div>
  <div class="abs fcol" style="left:356px"><h4>Resources</h4><a>Contact Us</a><a>Terms and Conditions</a><a>Data and Privacy Policy</a><a>Cookie Policy</a></div>
  <div class="abs fcol" style="left:500px"><h4>Get Connected</h4></div>
  <div class="abs social"><span></span><span></span><span></span><span></span></div>
  <div class="abs fbrand"><span class="fbrand-mark"></span><span class="fbrand-name">Lumara Maid Service</span></div>
  <div class="abs bottom"></div>
  <div class="abs copy">© 2014 Company Name&nbsp; All right reserved&nbsp; Term of Use</div>
</footer>

</body>
</html>
```